Veltrano.co - Polar Expeditions Specialists

We need a modern, visually striking business card for Veltrano.co, a company specialized in selling expedition cruises to the most remote regions on Earth, with a focus on the Arctic and Antarctica. The design should instantly communicate that the cardholder is an expert in polar travel. Use clean, premium aesthetics with cool tones like icy blue and white, possibly incorporating polar imagery (ice, glaciers, penguins, etc.)

Attached the logo

Contact Information for Business Card

Feels high-end and trustworthy.. Visually memorable — encourages people to keep it

Colors
0054AA
0677BA
7BADD7
CADEEF
E8F1F8

Requirements
Must have
• ice, glaciers, penguins, montains
Nice to have
• modern, transparente,

```html
<!DOCTYPE html>
<html lang="en">
<head>
<meta charset="utf-8">
<title>Veltrano.co — Business Card</title>
<link rel="stylesheet" href="https://fonts.googleapis.com/css2?family=Poppins:wght@400;600;700&family=Arimo:wght@400&display=swap">
<style>
  :root {
    --stage: #3d3d3d;
    --brand-blue: #3272b6;
    --deep-blue: #1f3f9e;
    --mid-blue: #2f66b3;
    --ice-blue: #5fd3ee;
    --text-grey: #4a4a4a;
    --muted-grey: #8a8a8a;
    --corner-grey: #5a5a5a;
    --paper: #ffffff;
  }
  * { box-sizing: border-box; margin: 0; padding: 0; }
  html, body { width: 1200px; height: 803px; overflow: hidden; background: var(--stage); }
  .stage { position: relative; width: 1200px; height: 803px; }
  .card {
    position: absolute; top: 241px; width: 550px; height: 320px;
    border-radius: 22px; overflow: hidden;
    box-shadow: 0 14px 34px rgba(0,0,0,.45);
  }
  .card--front { left: 35px; background: var(--paper); }
  .card--back { left: 615px; }
  .front-curve { position: absolute; inset: 0; width: 100%; height: 100%; }
  .identity { position: absolute; left: 40px; bottom: 38px; font-family: 'Poppins', sans-serif; }
  .brand { display: flex; align-items: center; gap: 10px; margin-bottom: 14px; }
  .brand-dot { width: 34px; height: 34px; border-radius: 50%; background: var(--brand-blue); flex: none; }
  .brand-name { font-size: 30px; font-weight: 700; color: var(--brand-blue); line-height: 1; }
  .brand-tagline { font-size: 9px; font-weight: 600; color: var(--brand-blue); margin-top: 3px; letter-spacing: .2px; }
  .person-name { font-size: 25px; font-weight: 700; color: var(--brand-blue); line-height: 1.1; }
  .person-role { font-family: 'Arimo', sans-serif; font-size: 13px; color: var(--muted-grey); margin-bottom: 10px; }
  .address, .contacts { font-family: 'Arimo', sans-serif; font-size: 13px; color: var(--text-grey); line-height: 1.35; }
  .address { margin-bottom: 10px; }
  .contact-row { display: flex; align-items: center; gap: 8px; }
  .contact-row svg { width: 11px; height: 11px; fill: var(--brand-blue); flex: none; }
  .back-pattern {
    width: 100%; height: 100%;
    background:
      radial-gradient(ellipse at 90% 15%, rgba(95,211,238,.55) 0%, rgba(95,211,238,0) 55%),
      linear-gradient(30deg, var(--deep-blue) 0%, var(--mid-blue) 40%, #3d8fd0 70%, var(--ice-blue) 100%);
  }
</style>
</head>
<body>
<main class="stage">
  <section class="card card--front" aria-label="Business card front">
    <svg class="front-curve" viewBox="0 0 550 320" preserveAspectRatio="none" aria-hidden="true">
      <path d="M420 0 H550 V120 Z" fill="var(--corner-grey)"/>
      <path d="M300 0 C430 0 550 40 550 110 V320 H470 C520 200 470 30 300 0 Z" fill="var(--brand-blue)"/>
      <path d="M0 0 H300 C470 30 520 200 470 320 H0 Z" fill="var(--paper)"/>
    </svg>
    <div class="identity">
      <div class="brand">
        <span class="brand-dot" aria-hidden="true"></span>
        <div>
          <div class="brand-name">Veltrano.co</div>
          <div class="brand-tagline">Polar Expeditions Specialists</div>
        </div>
      </div>
      <div class="person-name">Elena Marsh</div>
      <div class="person-role">President</div>
      <div class="address">4120 Harbor View Road<br>Northbay, Canada 58213</div>
      <div class="contacts">
        <div class="contact-row"><svg viewBox="0 0 12 12"><path d="M2 1h3l1 3-2 1a7 7 0 0 0 3 3l1-2 3 1v3c-6 0-9-3-9-9z"/></svg>555-210-4837</div>
        <div class="contact-row"><svg viewBox="0 0 12 12"><path d="M3 0h6v12H3z M4 1v9h4V1z"/></svg>555-391-7026</div>
        <div class="contact-row"><svg viewBox="0 0 12 12"><path d="M0 2h12v8H0z M1 3l5 4 5-4z"/></svg>hello@veltrano.co</div>
        <div class="contact-row"><svg viewBox="0 0 12 12"><circle cx="6" cy="6" r="6"/></svg>www.veltrano.co</div>
      </div>
    </div>
  </section>
  <section class="card card--back" aria-label="Business card back">
    <div class="back-pattern" role="img" aria-label="Repeating pattern of the polar brand emblem in rows, fading from deep navy at lower left to icy cyan at upper right, with one white emblem near the right edge"></div>
  </section>
</main>
</body>
</html>
```